Marlo K Dress Designs

My company (MarloK) designs and creates ladies fashion garments. I am a one person company at the moment with plans to bring on additional staff as the workload increases. At this stage I would prefer to focus on developing regional clients around Wellington, New Zealand so I can personalise the service. Expansion beyond the Wellington region is a dream in the future if all goes well with the website and the business.

I love working with people to create fashion garments for them that showcase their personalities and beauty, whatever their body type or physical appearance. I love helping my clients select the best designs, fabrics, colours and styles to look and feel the very best they can appropriate to the occasion they are dressing for. Sometimes its high-end fashion, sometimes its for daily wearing and on the odd occasion its just to be quirky and have fun with fashion. Clients typically want that special garment or outfit for special occasions like balls, weddings, racedays, reunions, concerts, anniversaries, receptions, functions and formal gatherings.

I have created a range of garments (about 12) which I would like to be showcased on the website. I can reproduce those garment showcased for clients, or I could work with the client to create a special one of a kind outfit for them, or reproduce off an existing dress design, or alter an existing outfit. have a customer focussed industry that focussing on bespoke garments rather than trying to compete with low cost mass produced ladies fashion garment.

I would like to have the prospective clients contact me by email directly from the website and work with them to design, quote, produce and tailor what they want. These fashion garments will be more expensive than off-the-rack garments readily available in shops or online. But they will be specifically tailored for the individuals. Clients will be given a quote based upon the design, type and quantity of the material used before I create the garment.

A couple of quotes in regards to my fashion design that expresses my love for creating and producing great garments for people:
- Percy Haldane - 'You can never be overdressed or overeducated.'
- Pipsy - 'There's no need to dress like everybody else. Its much more fun to create your own.'
- Carlo Benvetti- 'I really want to make clothes that are feminine and help women look beautiful.'

I want to have this website hosted on a server and I want to be able to amend and update the photos and other content myself.

I like a mix of old and new sewing related art/images.

My email address and phone number should be in the contact page. They are shown in the cards below. I will upload photos of my creations soon.

Industry/Entity Type

Fashion

Coding

Coded - Design and coding required

Number of Pages Required

3 page

Colors

Designer to choose colors to be used in the design.

Requirements
Must have
• Blog
• Services (Formal Dresses, Alterations, Buisness attire, every day wear, style consults)
Should not have
• Products

```html
<!DOCTYPE html>
<html lang="en">
<head>
<meta charset="utf-8">
<title>Marlo K Dress Designs</title>
<link rel="stylesheet" href="https://fonts.googleapis.com/css2?family=Playfair+Display:ital,wght@0,400;0,700;1,400&family=Lato:wght@400;700&display=swap">
<style>
:root{
  --brand:#a8274f;
  --brand-soft:#c2456b;
  --ink:#2b2b2b;
  --muted:#6b6b6b;
  --dark:#2a2a2a;
  --darker:#1f1f1f;
  --light:#efefef;
  --white:#ffffff;
  --line:#d8d8d8;
}
*{box-sizing:border-box;margin:0;padding:0}
html,body{width:1200px;height:2856px;overflow:hidden;background:var(--white)}
body{font-family:"Lato",sans-serif;color:var(--ink);position:relative}
.serif{font-family:"Playfair Display",serif}

/* Header */
.site-header{height:152px;position:relative}
.logo{position:absolute;left:132px;top:14px;font-family:"Playfair Display",serif;font-size:86px;color:var(--brand);font-weight:400;letter-spacing:-1px}
.contact-top{position:absolute;right:132px;top:36px;display:flex;gap:38px;font-size:21px;color:var(--ink)}
.contact-top span{display:flex;align-items:center;gap:10px}
.main-nav{position:absolute;right:132px;top:108px;display:flex;gap:40px;font-family:"Playfair Display",serif;font-size:19px}
.main-nav a{color:var(--ink);text-decoration:none;padding-bottom:6px}
.main-nav a.active{border-bottom:3px solid var(--brand)}

/* Hero */
.hero{position:relative;height:616px;overflow:hidden}
.hero-photo{position:absolute;inset:0;background:linear-gradient(100deg,#5e5a55 0%,#8a7f76 22%,#d9c0c4 42%,#c9a3ab 52%,#6f5e54 70%,#4a3e38 100%)}
.hero-quote{position:absolute;left:692px;top:380px;width:396px;height:160px;background:rgba(255,255,255,.88);padding:26px 30px;font-family:"Playfair Display",serif}
.hero-quote p{font-size:27px;line-height:1.3;color:var(--ink)}
.hero-quote cite{display:block;text-align:right;font-style:italic;color:var(--brand-soft);font-size:24px;margin-top:6px}
.hero-arrow{position:absolute;top:448px}
.hero-arrow.left{left:8px}.hero-arrow.right{right:8px}

/* Welcome */
.welcome{position:relative;height:464px}
.welcome h1{position:absolute;left:132px;top:78px;font-family:"Playfair Display",serif;font-weight:400;font-size:50px;color:var(--brand)}
.welcome .lead{position:absolute;left:132px;top:152px;width:440px;font-size:22px;line-height:1.35}
.welcome .body-text{position:absolute;left:132px;top:226px;width:440px;font-size:15px;line-height:1.6;color:var(--muted)}
.btn{position:absolute;left:132px;top:346px;width:104px;height:46px;border:1px solid var(--line);font-family:"Playfair Display",serif;font-size:16px;color:var(--muted);display:flex;align-items:center;justify-content:center}
.welcome-photo{position:absolute;left:636px;top:72px;width:436px;height:312px;background:linear-gradient(135deg,#e3e6ea 0%,#b9c4cf 40%,#7fa0bd 70%,#d7dde2 100%)}

/* Garments */
.garments{position:relative;height:896px;background:var(--dark)}
.garments h2{position:absolute;top:60px;width:100%;text-align:center;font-family:"Playfair Display",serif;font-weight:400;font-size:46px;color:var(--white)}
.garment-grid{position:absolute;left:132px;top:140px;display:grid;grid-template-columns:repeat(4,216px);gap:20px 24px}
.garment-card{height:216px;background:var(--white);padding:6px}
.garment-card .photo{height:168px}
.garment-card .label{text-align:center;font-family:"Playfair Display",serif;font-size:15px;margin-top:12px;color:var(--ink)}
.t1{background:linear-gradient(#f2f2f2,#3a3a3a)}.t2{background:linear-gradient(#dcd8d2,#f4efe8)}
.t3{background:linear-gradient(#e9dcc4,#c9b18a)}.t4{background:linear-gradient(#9ec7e4,#5a4a44)}
.t5{background:linear-gradient(#8a7d74,#5d504a)}.t6{background:linear-gradient(#d8d2cc,#38302c)}
.t7{background:linear-gradient(#e6e3dc,#8d8b86)}.t8{background:linear-gradient(#7aa7c9,#b85c5c)}
.t9{background:linear-gradient(#e9e5df,#b69a86)}.t10{background:linear-gradient(#bdbdb8,#77736c)}
.t11{background:linear-gradient(#f1ece6,#2a2a2a)}.t12{background:linear-gradient(#d9cfc6,#8c6c62)}

/* Reviews */
.reviews{position:relative;height:512px}
.reviews h2{position:absolute;top:84px;width:100%;text-align:center;font-family:"Playfair Display",serif;font-weight:400;font-size:46px;color:var(--brand)}
.review-box{position:absolute;left:132px;top:144px;width:936px;height:200px;background:var(--light);padding:32px 60px;text-align:center;font-family:"Playfair Display",serif;font-size:22px;line-height:1.55;color:var(--ink)}
.avatar{position:absolute;left:552px;top:300px;width:96px;height:96px;border-radius:50%;border:4px solid var(--white);background:linear-gradient(#e8cfa8,#c9a57d)}
.reviewer{position:absolute;top:412px;width:100%;text-align:center;font-size:15px;color:var(--brand-soft)}
.rev-arrow{position:absolute;top:232px}
.rev-arrow.left{left:40px}.rev-arrow.right{right:40px}

/* Footer */
.footer-info{height:104px;background:var(--light);display:flex;justify-content:center;align-items:center;gap:40px;font-size:17px;color:var(--ink)}
.footer-info span{display:flex;align-items:center;gap:10px}
.footer-info .sep{color:var(--line)}
.footer-bottom{position:relative;height:112px;background:var(--darker);color:#bbbbbb}
.footer-links{position:absolute;left:132px;top:30px;font-size:14px;display:flex;gap:10px}
.copyright{position:absolute;left:132px;top:60px;font-size:13px;color:#888}
.social{position:absolute;right:132px;top:36px;display:flex;gap:22px}
.social span{width:22px;height:22px;border-radius:50%;background:#9a9a9a;display:block}
</style>
</head>
<body>

<header class="site-header">
  <div class="logo">Marlo K</div>
  <div class="contact-top">
    <span><svg width="20" height="15" viewBox="0 0 20 15"><rect x="0" y="0" width="20" height="15" rx="2" fill="#2b2b2b"/><path d="M1 1l9 7 9-7" stroke="#fff" stroke-width="1.6" fill="none"/></svg>marlokdesigner@example.com</span>
    <span><svg width="16" height="18" viewBox="0 0 16 18"><path d="M3 1l3 0 2 5-2 2c1 2 3 4 5 5l2-2 3 2v3c-8 0-16-7-13-15z" fill="#2b2b2b"/></svg>021 555 014</span>
  </div>
  <nav class="main-nav">
    <a class="active" href="#">Home</a><a href="#">Our Garments</a><a href="#">Reviews</a><a href="#">Blog</a><a href="#">About Us</a><a href="#">Contact Us</a>
  </nav>
</header>

<section class="hero">
  <div class="hero-photo" role="img" aria-label="Woman in a pale pink jacket and sunglasses standing before a brick wall"></div>
  <blockquote class="hero-quote">
    <p>“ You can never be overdressed or overeducated „</p>
    <cite>– Percy Haldane</cite>
  </blockquote>
  <svg class="hero-arrow left" width="20" height="40" viewBox="0 0 20 40"><path d="M15 6L5 20l10 14" stroke="#fff" stroke-width="3" fill="none"/></svg>
  <svg class="hero-arrow right" width="20" height="40" viewBox="0 0 20 40"><path d="M5 6l10 14L5 34" stroke="#fff" stroke-width="3" fill="none"/></svg>
</section>

<section class="welcome">
  <h1>Welcome to Marlo K</h1>
  <p class="lead">Vestibulum condimentum, risus ut posuere cursus, velit justo accumsan sem.</p>
  <p class="body-text">Phasellus consequat sagittis nisl suscipit feugiat. Cras egestas nunc non hendrerit ultricies eu ante. Praesent iaculis facilisis purus, quis aliquet diam consequat quis. Nulla porta velit, id mollis massa imperdiet sed. Fusce eget neque vel ipsum. Integer fermentum in magna congue.</p>
  <div class="btn">Read More</div>
  <div class="welcome-photo" role="img" aria-label="Hands sewing fabric beside spools of thread"></div>
</section>

<section class="garments">
  <h2>Our Garments</h2>
  <div class="garment-grid">
    <div class="garment-card"><div class="photo t1" role="img" aria-label="Model in black outfit"></div><div class="label">Aenean facilisis</div></div>
    <div class="garment-card"><div class="photo t2" role="img" aria-label="Bride in wedding gown"></div><div class="label">Wedding Garments</div></div>
    <div class="garment-card"><div class="photo t3" role="img" aria-label="Woman in light summer dress"></div><div class="label">Cras sollicitudin</div></div>
    <div class="garment-card"><div class="photo t4" role="img" aria-label="Woman in reception dress"></div><div class="label">Reception Garments</div></div>
    <div class="garment-card"><div class="photo t5" role="img" aria-label="Clothing rail with garments"></div><div class="label">Etiam mattis</div></div>
    <div class="garment-card"><div class="photo t6" role="img" aria-label="Woman in dark coat"></div><div class="label">Nulla facilisi</div></div>
    <div class="garment-card"><div class="photo t7" role="img" aria-label="Woman in casual wear"></div><div class="label">Aliquam erat</div></div>
    <div class="garment-card"><div class="photo t8" role="img" aria-label="Two women in bright outfits"></div><div class="label">Pellentesque</div></div>
    <div class="garment-card"><div class="photo t9" role="img" aria-label="Group of women in dresses"></div><div class="label">Etiam augue</div></div>
    <div class="garment-card"><div class="photo t10" role="img" aria-label="Woman on stairs in grey outfit"></div><div class="label">Vivamus lacus</div></div>
    <div class="garment-card"><div class="photo t11" role="img" aria-label="Patterned function dress"></div><div class="label">Functions Garments</div></div>
    <div class="garment-card"><div class="photo t12" role="img" aria-label="Woman in evening dress"></div><div class="label">Fusce vitae</div></div>
  </div>
</section>

<section class="reviews">
  <h2>Reviews</h2>
  <div class="review-box">“ Maecenas vel tortor accumsan quam varius imperdiet vel eget elit. Aenean facilisis tincidunt lectus, id dictum nisl luctus eget. Vivamus efficitur ex condimentum, malesuada eros eget, feugiat nibh „</div>
  <div class="avatar" role="img" aria-label="Reviewer portrait"></div>
  <div class="reviewer">Emily, City</div>
  <svg class="rev-arrow left" width="16" height="30" viewBox="0 0 16 30"><path d="M12 4L4 15l8 11" stroke="#bbb" stroke-width="2.5" fill="none"/></svg>
  <svg class="rev-arrow right" width="16" height="30" viewBox="0 0 16 30"><path d="M4 4l8 11-8 11" stroke="#bbb" stroke-width="2.5" fill="none"/></svg>
</section>

<footer>
  <div class="footer-info">
    <span><svg width="14" height="20" viewBox="0 0 14 20"><path d="M7 0C3 0 0 3 0 7c0 5 7 13 7 13s7-8 7-13c0-4-3-7-7-7z" fill="#2b2b2b"/><circle cx="7" cy="7" r="2.5" fill="#efefef"/></svg>24 Building name, Street name, City Zipcode</span>
    <span class="sep">|</span>
    <span><svg width="14" height="16" viewBox="0 0 16 18"><path d="M3 1l3 0 2 5-2 2c1 2 3 4 5 5l2-2 3 2v3c-8 0-16-7-13-15z" fill="#2b2b2b"/></svg>Phone: 021 555 014</span>
    <span class="sep">|</span>
    <span><svg width="18" height="13" viewBox="0 0 20 15"><rect width="20" height="15" rx="2" fill="#2b2b2b"/><path d="M1 1l9 7 9-7" stroke="#efefef" stroke-width="1.6" fill="none"/></svg>Email : marlokdesigner@example.com</span>
  </div>
  <div class="footer-bottom">
    <div class="footer-links"><span>Home</span>|<span>Our Garments</span>|<span>Reviews</span>|<span>Blog</span>|<span>About Us</span>|<span>Contacts</span></div>
    <div class="copyright">Copyright © 2018 Marlo K. All rights reserved</div>
    <div class="social" aria-label="Social links"><span></span><span></span><span></span></div>
  </div>
</footer>

</body>
</html>
```